Dental Practice Billboard Design

We are a newer dental practice in need of a simple but appealing billboard for our growing dental practice to attract new patients. The practice is owned by husband and wife dentists and is family friendly in a small town in Kentucky. We try to be very friendly and caring to our patients. Would prefer a blue background for the billboard and our tooth logo to be prominent. We are partial to the Patua One font used in the image below but please feel free to tweak it as you deem necessary. The shape of the uppercase D and lowercase g are why we like that font, so fonts with a similarly shaped “D” and “g” would work as well. Please include our phone number (555) 847-1390. Please see our website Harlowbrookdentistry.example for more info on the practice if needed. Thank you! Looking forward to seeing your creation.
Updates

The dimensions will be 12ft x 24ft (3.6576m x 7.3152m). Apologies for not including this in the original prompt. Thank you all for your submissions.

Industry/Entity Type

Dental

Font styles to use
Other font styles liked:
• Patua One

Colors
0054AA
0677BA
7BADD7
CADEEF
E8F1F8
0094D4
00A9DD
6FCCEA
C7EBF8
E9F6FB
00AB8E
00BBA5
67D7C9
C6EFE9
E9F9F6
59FF00
82FF00
B8FF75
E3FFCB
F4FFEA

Requirements
Must have
• Phone number, website, Logo, Practice name “Harlow Brook Dentistry”
Should not have
• A tagline or slogan

```html
<!DOCTYPE html>
<html lang="en">
<head>
<meta charset="utf-8">
<title>Harlow Brook Dentistry Billboard</title>
<link rel="stylesheet" href="https://fonts.googleapis.com/css2?family=Patua+One&family=Poppins:wght@600;700&display=swap">
<style>
  :root {
    --page-bg: #9a9a9a;
    --sky-light: #e4f1fa;
    --sky-mid: #bfdff3;
    --sky-deep: #97cbec;
    --brand-blue: #0054aa;
    --band-blue: #0a52b8;
    --brand-green: #1aad1a;
    --white: #ffffff;
    --photo-warm: #d9cbbd;
    --photo-cool: #8fb3d4;
  }
  * { margin: 0; padding: 0; box-sizing: border-box; }
  html, body { width: 995px; height: 1200px; overflow: hidden; }
  body { background: var(--page-bg); position: relative; }

  .billboard {
    position: absolute;
    left: 48px;
    top: 365px;
    width: 900px;
    height: 470px;
    overflow: hidden;
    background: radial-gradient(ellipse at 70% 30%, var(--sky-light) 0%, var(--sky-mid) 55%, var(--sky-deep) 100%);
    box-shadow: 18px 22px 30px rgba(0,0,0,0.35);
  }

  .family-photo {
    position: absolute;
    left: 12px;
    top: 60px;
    width: 470px;
    height: 410px;
    border-radius: 40px 40px 0 0;
    background: linear-gradient(160deg, var(--photo-warm) 0%, #e9e6e2 40%, var(--photo-cool) 100%);
  }

  .practice-name {
    position: absolute;
    left: 470px;
    width: 430px;
    top: 60px;
    height: 200px;
    display: flex;
    align-items: center;
    justify-content: center;
    gap: 18px;
  }
  .practice-name .mark-dot {
    width: 28px; height: 28px;
    border-radius: 50%;
    background: var(--brand-green);
    flex: none;
  }
  .practice-name span {
    font-family: "Patua One", serif;
    font-size: 52px;
    line-height: 1.08;
    color: var(--brand-blue);
  }

  .phone-band {
    position: absolute;
    left: 440px;
    top: 293px;
    width: 460px;
    height: 98px;
    background: var(--band-blue);
    clip-path: polygon(40px 0, 100% 0, 100% 100%, 0 100%);
    display: flex;
    align-items: center;
    justify-content: flex-end;
    padding-right: 28px;
    gap: 10px;
  }
  .phone-band .phone-icon { width: 40px; height: 40px; flex: none; }
  .phone-band .phone-number {
    font-family: "Poppins", sans-serif;
    font-weight: 600;
    font-size: 46px;
    color: var(--white);
    letter-spacing: 1px;
  }

  .web-band {
    position: absolute;
    left: 360px;
    top: 391px;
    width: 540px;
    height: 79px;
    background: var(--brand-green);
    display: flex;
    align-items: center;
    justify-content: flex-end;
    padding-right: 32px;
  }
  .web-band .website {
    font-family: "Poppins", sans-serif;
    font-weight: 600;
    font-size: 25px;
    color: var(--white);
    letter-spacing: 1px;
  }
</style>
</head>
<body>
  <div class="billboard">
    <div class="family-photo" role="img" aria-label="Photo of a smiling family of four sitting together on the floor"></div>

    <div class="practice-name">
      <div class="mark-dot"></div>
      <span>Harlow Brook<br>Dentistry</span>
    </div>

    <div class="phone-band">
      <svg class="phone-icon" viewBox="0 0 40 40" aria-hidden="true">
        <circle cx="20" cy="20" r="19" fill="#1aad1a"/>
        <path d="M14 10c1-.6 2-.4 2.6.6l2 3.4c.5.9.3 2-.5 2.6l-1.4 1c.9 2.2 2.5 4 4.6 5.1l1.1-1.3c.7-.8 1.8-1 2.7-.4l3.3 2.1c1 .6 1.2 1.7.5 2.6l-1.3 1.6c-1 1.2-2.6 1.6-4.1 1.1C17 26.3 12.6 21.6 11 15.2c-.4-1.5.1-3 1.3-3.9z" fill="#ffffff"/>
        <path d="M22 12a7 7 0 0 1 6 6M22 8a11 11 0 0 1 10 10" stroke="#ffffff" stroke-width="1.8" fill="none" stroke-linecap="round"/>
      </svg>
      <span class="phone-number">555-847-1390</span>
    </div>

    <div class="web-band">
      <span class="website">harlowbrookdentistry.example</span>
    </div>
  </div>
</body>
</html>
```